Business Card Design & Gift cards, Gift Cert, Donation Card

Retail Gift Store-in addition to Business Cards we'd like sequenced 2 sided Gift cards, Gift Certificate Cards, and Donation Cards.please see examples and email for clarificationlogos attached with examples-
Gift Card, Gift Certificate and Donation Card will all be same style just differant upper right title, with back side info as example.
business card, as example is single sided.
looking for additional ideas for layout

Industry/Entity Type

Business

Contact Information for Business Card

211 Newman St.East Tawas, MI 48730989.362.8730Office@BrewKrew.com

Requirements
Must have
• Blue as per example
• Logos provided
• like gradiant background

```html
<!DOCTYPE html>
<html lang="en">
<head>
<meta charset="utf-8">
<title>Tillow Marsh – Business Card</title>
<link href="https://fonts.googleapis.com/css2?family=Patrick+Hand&display=swap" rel="stylesheet">
<style>
  :root {
    --royal: #0b3fd9;
    --royal-deep: #0a36c4;
    --panel-light: #eef3f8;
    --panel-mid: #c9dcef;
    --ink-light: #ffffff;
    --name-blue: #1a45d0;
    --art-blue: #6f8fe6;
    --art-pale: #b9cbf1;
    --stage: #e4e6ea;
  }
  * { margin: 0; padding: 0; box-sizing: border-box; }
  html, body { width: 1200px; height: 892px; overflow: hidden; }
  body {
    background: var(--stage);
    font-family: "Patrick Hand", "Comic Sans MS", cursive;
    position: relative;
  }
  .card {
    position: absolute;
    width: 700px;
    height: 400px;
    box-shadow: 0 6px 18px rgba(0,0,0,0.18);
  }
  /* Front */
  .card-front {
    left: 60px; top: 40px;
    background: var(--royal);
    padding: 22px;
  }
  .front-panel {
    position: relative;
    width: 100%; height: 100%;
    background: linear-gradient(160deg, var(--panel-light) 0%, #dde8f3 55%, var(--panel-mid) 100%);
  }
  .contact-block {
    position: absolute;
    top: 0; right: 34px;
    width: 300px; height: 205px;
    background: var(--royal-deep);
    display: flex;
    flex-direction: column;
    justify-content: center;
    padding-left: 56px;
    gap: 6px;
    color: var(--ink-light);
    font-size: 21px;
    line-height: 1.15;
  }
  .contact-row { display: flex; align-items: flex-start; gap: 12px; }
  .contact-icon {
    flex: none;
    width: 14px; height: 14px;
    margin-top: 5px;
    background: var(--ink-light);
    border-radius: 2px;
    display: flex; align-items: center; justify-content: center;
  }
  .contact-icon svg { width: 10px; height: 10px; }
  .brand-name {
    position: absolute;
    left: 24px; top: 152px;
    font-size: 40px;
    letter-spacing: 2px;
    color: var(--name-blue);
    line-height: 1;
    white-space: nowrap;
  }
  .mascot-art {
    position: absolute;
    left: 24px; top: 222px;
    width: 330px; height: 116px;
    background: linear-gradient(90deg, var(--art-blue), var(--art-pale));
    border-radius: 6px;
  }
  /* Back */
  .card-back {
    left: 440px; top: 452px;
    background: linear-gradient(200deg, #f3f6f9 0%, #dce7f2 50%, #b9d2ea 100%);
    display: flex; align-items: center; justify-content: center;
  }
  .back-name {
    font-size: 110px;
    letter-spacing: 4px;
    color: var(--name-blue);
    line-height: 1;
    white-space: nowrap;
  }
</style>
</head>
<body>
  <section class="card card-front">
    <div class="front-panel">
      <div class="contact-block">
        <div class="contact-row">
          <span class="contact-icon"><svg viewBox="0 0 10 10"><path d="M2 1h2l1 2-1 1a5 5 0 0 0 2 2l1-1 2 1v2c-4 0-7-3-7-7z" fill="#0a36c4"/></svg></span>
          <span>989.517.4296</span>
        </div>
        <div class="contact-row">
          <span class="contact-icon"><svg viewBox="0 0 10 10"><rect x="1" y="2" width="8" height="6" fill="none" stroke="#0a36c4" stroke-width="1.2"/><path d="M1 2l4 3 4-3" fill="none" stroke="#0a36c4" stroke-width="1.2"/></svg></span>
          <span>Office@TillowMarsh.com</span>
        </div>
        <div class="contact-row">
          <span class="contact-icon"><svg viewBox="0 0 10 10"><path d="M5 1a3 3 0 0 1 3 3c0 2-3 5-3 5S2 6 2 4a3 3 0 0 1 3-3z" fill="#0a36c4"/></svg></span>
          <span>482 Larkfield Ave.<br>Pine Harbor, MI 48691</span>
        </div>
      </div>
      <div class="brand-name">TILLOW MARSH</div>
      <div class="mascot-art" role="img" aria-label="Illustration of a dancing figure in front of a rising sun"></div>
    </div>
  </section>

  <section class="card card-back">
    <div class="back-name">TILLOW MARSH</div>
  </section>
</body>
</html>
```